Redesign of business card for Cedar Ridge Mechanical

We are looking for a new design for our business cards for Cedar Ridge Mechanical. We are a plumbing & HVAC construction company, operating on the West Coast of Canada and USA. Logo attached.
Industry/Entity Type
Construction - Plumbing & HVAC
Contact Information for Business Card
Name, address, phone numbers, email, website address
Look and feel
Each slider illustrates characteristics of the customer's brand and the style your logo design should communicate.

```html
<!DOCTYPE html>
<html lang="en">
<head>
<meta charset="utf-8">
<title>Cedar Ridge Mechanical – Business Card</title>
<link href="https://fonts.googleapis.com/css2?family=Open+Sans:wght@400;700&family=Montserrat:wght@400&display=swap" rel="stylesheet">
<style>
  :root {
    --backdrop: #d6d6d6;
    --card: #ffffff;
    --ink: #000000;
    --grey-band: #8c8c8c;
    --on-dark: #ffffff;
  }
  * { margin: 0; padding: 0; box-sizing: border-box; }
  html, body { width: 1200px; height: 896px; overflow: hidden; }
  body {
    background: var(--backdrop);
    position: relative;
    font-family: "Open Sans", sans-serif;
    color: var(--ink);
  }
  .card {
    position: absolute;
    left: 334px;
    width: 527px;
    height: 301px;
    background: var(--card);
    border-radius: 24px;
    overflow: hidden;
  }
  .card--front { top: 126px; }
  .card--back { top: 475px; }

  .brand { display: flex; align-items: center; gap: 14px; }
  .brand__mark { background: var(--ink); flex: none; }
  .brand__name {
    font-family: "Open Sans", sans-serif;
    font-weight: 700;
    color: var(--ink);
    text-transform: uppercase;
    line-height: 1.1;
  }

  .card--front .brand {
    position: absolute;
    inset: 0;
    justify-content: center;
  }
  .card--front .brand__mark { width: 54px; height: 54px; }
  .card--front .brand__name { font-size: 27px; }

  .card--back .brand {
    position: absolute;
    left: 20px;
    top: 30px;
    width: 230px;
  }
  .card--back .brand__mark { width: 40px; height: 40px; }
  .card--back .brand__name { font-size: 19px; }

  .person {
    position: absolute;
    right: 20px;
    top: 28px;
    text-align: right;
  }
  .person__name { font-size: 19.5px; font-weight: 700; line-height: 1.2; }
  .person__title { font-size: 13.5px; font-weight: 400; line-height: 1.4; }

  .wave { position: absolute; inset: 0; width: 100%; height: 100%; }

  .contact {
    position: absolute;
    right: 20px;
    top: 170px;
    text-align: right;
    font-family: "Montserrat", sans-serif;
    font-size: 13.8px;
    color: var(--on-dark);
    line-height: 20px;
  }
  .contact__address { margin-bottom: 15px; }
  .contact__line { display: flex; justify-content: flex-end; align-items: center; gap: 6px; }
  .contact__icon { width: 12px; height: 12px; fill: var(--on-dark); }
</style>
</head>
<body>

  <section class="card card--front">
    <div class="brand">
      <span class="brand__mark"></span>
      <span class="brand__name">Cedar Ridge Mechanical</span>
    </div>
  </section>

  <section class="card card--back">
    <svg class="wave" viewBox="0 0 897 512" preserveAspectRatio="none" aria-hidden="true">
      <path d="M0,404 C250,440 400,380 550,280 C680,196 800,180 897,182 L897,512 L0,512 Z" fill="var(--ink)"/>
      <path d="M0,414 C250,452 410,392 560,294 C690,214 800,206 897,210 L897,512 L0,512 Z" fill="var(--card)"/>
      <path d="M0,420 C255,458 415,398 565,300 C695,220 800,212 897,218 L897,512 L0,512 Z" fill="var(--grey-band)"/>
      <path d="M0,448 C262,478 422,410 572,312 C702,230 805,224 897,230 L897,512 L0,512 Z" fill="var(--card)"/>
      <path d="M0,454 C268,484 428,416 578,318 C708,236 808,230 897,236 L897,512 L0,512 Z" fill="var(--ink)"/>
    </svg>

    <div class="brand">
      <span class="brand__mark"></span>
      <span class="brand__name">Cedar Ridge<br>Mechanical</span>
    </div>

    <div class="person">
      <p class="person__name">DANIEL HAYES</p>
      <p class="person__title">Managing Director</p>
    </div>

    <div class="contact">
      <p class="contact__address">Your address, City<br>State, Zip 1234</p>
      <p class="contact__line">123 456 789
        <svg class="contact__icon" viewBox="0 0 24 24"><path d="M6.6 10.8a15.1 15.1 0 0 0 6.6 6.6l2.2-2.2a1 1 0 0 1 1-.25 11.4 11.4 0 0 0 3.6.57 1 1 0 0 1 1 1V20a1 1 0 0 1-1 1A17 17 0 0 1 3 4a1 1 0 0 1 1-1h3.5a1 1 0 0 1 1 1c0 1.25.2 2.45.57 3.57a1 1 0 0 1-.25 1z"/></svg>
      </p>
      <p class="contact__line">info@yourgmail.com
        <svg class="contact__icon" viewBox="0 0 24 24"><path d="M2 5h20v14H2z M4 7v.5l8 5 8-5V7l-8 5z" fill-rule="evenodd"/></svg>
      </p>
      <p class="contact__line">www.yourwebsite.com
        <svg class="contact__icon" viewBox="0 0 24 24"><path d="M12 2a10 10 0 1 0 0 20 10 10 0 0 0 0-20zm0 2c1.2 1.5 2 3.6 2.2 6H9.8C10 7.6 10.8 5.5 12 4zM4.1 13h3.7c.1 2.3.7 4.3 1.7 5.8A8 8 0 0 1 4.1 13zm0-2a8 8 0 0 1 5.4-5.8c-1 1.5-1.6 3.5-1.7 5.8zm5.7 2h4.4c-.2 2.4-1 4.5-2.2 6-1.2-1.5-2-3.6-2.2-6zm6.4 0h3.7a8 8 0 0 1-5.4 5.8c1-1.5 1.6-3.5 1.7-5.8zm0-2c-.1-2.3-.7-4.3-1.7-5.8a8 8 0 0 1 5.4 5.8z"/></svg>
      </p>
    </div>
  </section>

</body>
</html>
```